Advanced Therapeutic Massage Therapist

I need a business card advertising my massage services as an advanced therapeutic massage therapist. I offer advanced therapeutic massage, swedish and deep tissue. I want to create a simple, professional and feminine card. I like bright colours and creativity.

I prefer a bold and experimental approach rather than something status-quo. A card to suggest therapeutic healing through dynamic massage. Motifs, shapes or layout which suggest movement and flow.
Updates

Target Market(s)

Everybody!

Industry/Entity Type

Health And Wellness

Contact Information for Business Card

The card should include:
My name, logo, services offered and my contact details.

Sláine Dunleavy
Massage Therapist

- Swedish - Deep Tissue - Advanced Therapeutic

Phone: (+353) 87 216 4093
Email: regenerate@slainedunleavy-example.com
Website: www.slainedunlevy-example.com

Font styles to use
Serif
Sans Serif
Decorative
Script

Colors

Designer to choose colors to be used in the design.

Requirements
Must have
• An example may contain something like this, yet concise:
• "Sláine Dunleavy
• Massage Therapist
• - Swedish - Deep Tissue - Advanced Therapeutic"
Nice to have
• This sentence is optional:
• Imagery such as a logo or symbol. I have attached a file containing a logo I had produced however the name is incorrect now as it is "Sláine" not "Nelly". It could be edited to change it to Sláine.
• I have sent the file as .psd .jpg. .pdf and .png
• I like when the card conveys energy, movement, pressure points, flow etc.
• I just like the designer to follow their own style and ideas. I like bright colours but must have a lot of a base colour to offset it. I really prefer them to follow their own inspiration. That is my preference.
Should not have
• Pine trees, non-native trees to Britain and Ireland, exotic flowers or animals that are not native to Britain and Ireland.
• I don't like brown as the background colour of the card.
• The cars shouldn't look like a wedding invitation i.e too many floral type designs.

```html
<!DOCTYPE html>
<html lang="en">
<head>
<meta charset="utf-8">
<title>Sláine Dunleavy – Massage Therapist Business Card</title>
<link rel="stylesheet" href="https://fonts.googleapis.com/css2?family=Open+Sans:wght@400;700&family=Great+Vibes&family=Quicksand:wght@400&display=swap">
<style>
  :root {
    --stage: #ecebea;
    --card-light: #ffffff;
    --card-dark: #18191d;
    --ink: #1c1c1c;
    --ink-soft: #dcdcde;
    --teal: #a9d6cc;
    --gold: #b98a3c;
  }
  * { margin: 0; padding: 0; box-sizing: border-box; }
  html, body {
    width: 1200px;
    height: 900px;
    overflow: hidden;
    background: var(--stage);
  }
  .stage {
    position: relative;
    width: 1200px;
    height: 900px;
  }
  .card {
    position: absolute;
    border-radius: 16px;
    box-shadow: 0 6px 18px rgba(0,0,0,0.15);
  }
  .card-back {
    left: 78px;
    top: 35px;
    width: 588px;
    height: 364px;
    background: var(--card-light);
    color: var(--ink);
    font-family: "Open Sans", sans-serif;
    text-align: center;
  }
  .contact {
    position: absolute;
    top: 116px;
    left: 0;
    right: 0;
    font-size: 16px;
    line-height: 24px;
  }
  .services {
    position: absolute;
    top: 218px;
    left: 0;
    right: 0;
    font-size: 16px;
    font-weight: 700;
    line-height: 24px;
  }
  .services .dot {
    display: inline-block;
    width: 9px;
    height: 9px;
    border-radius: 50%;
    background: var(--ink);
    margin: 0 12px 2px;
    vertical-align: middle;
  }
  .card-front {
    left: 390px;
    top: 506px;
    width: 565px;
    height: 350px;
    background: var(--card-dark);
    text-align: center;
  }
  .mark {
    position: absolute;
    left: 206px;
    top: 78px;
    width: 152px;
    height: 152px;
  }
  .name {
    position: absolute;
    top: 232px;
    left: 0;
    right: 0;
    font-family: "Great Vibes", cursive;
    font-weight: 400;
    font-size: 30px;
    color: var(--ink-soft);
    line-height: 36px;
  }
  .role {
    position: absolute;
    top: 265px;
    left: 0;
    right: 0;
    font-family: "Quicksand", sans-serif;
    font-size: 13px;
    letter-spacing: 1.5px;
    color: var(--ink-soft);
  }
</style>
</head>
<body>
<main class="stage">
  <section class="card card-back">
    <p class="contact">(+353) 87 216 4093<br>regenerate@slainedunleavy-example.com<br>www.slainedunlevy-example.com</p>
    <p class="services">Swedish<span class="dot"></span>Deep Tissue<br>Advanced Therapeutic</p>
  </section>

  <section class="card card-front">
    <svg class="mark" viewBox="0 0 152 152" role="img" aria-label="Brand emblem area for Sláine Dunleavy">
      <circle cx="76" cy="76" r="72" fill="var(--teal)" stroke="var(--gold)" stroke-width="4"/>
    </svg>
    <h1 class="name">Sláine Dunleavy</h1>
    <p class="role">massage therapist</p>
  </section>
</main>
</body>
</html>
```